Dynamic Business Card for Sports Supplements Company

Hi! I'm looking for an awesome business card to match my existing sports supplement company. I have uploaded my current company logo and screenshot of the front page of my website.

I would like to have something dynamic and interesting and utilize the colors in the website - the reds and purples

The business card should be double sided and focus on a unique eye-catching design on the back and include all the relevant company info.

Most importantly, it should say somewhere: "Sign up on our website for a coupon code."

Target Market(s)

Mostly for women gym goers but it shouldn't be too feminine. It should be in keeping with the website design. It should flow and clearly be connected to it

Industry/Entity Type

Business

Contact Information for Business Card

Lorraine K. Vestal
CEO
LVestal@Quorvanexco.com
www.quorvanexco.com
555.417.3820
P.O. Box 47315
Larkfield, Ondera 00000

Sign up on our website for a coupon code

Font styles to use
Serif
Sans Serif
Other font styles liked:
• Novecento font family and "Quorvanex" is in AR Destine font

Requirements
Must have
• One side should be a bold Quorvanex logo design. Even just the symbol itself may be o.k. (see attached file)

```html
<!DOCTYPE html>
<html lang="en">
<head>
<meta charset="utf-8">
<title>Quorvanex Business Card</title>
<link href="https://fonts.googleapis.com/css2?family=Oswald:wght@400;500;600&family=Work+Sans:wght@400;500&display=swap" rel="stylesheet">
<style>
  :root {
    --backdrop: #2b2b2d;
    --card-dark: #1c1c1c;
    --card-light: #ffffff;
    --brand-red: #e0262b;
    --ink-dark: #3d3d3d;
    --ink-mid: #555555;
    --ink-light: #ffffff;
  }
  * { margin: 0; padding: 0; box-sizing: border-box; }
  html, body {
    width: 1200px; height: 1000px; overflow: hidden;
    background: var(--backdrop);
  }
  .canvas { position: relative; width: 1200px; height: 1000px; }
  .card {
    position: absolute; left: 250px; width: 700px; height: 400px;
    box-shadow: 0 12px 30px rgba(0,0,0,0.45);
  }
  /* Back side */
  .card--back {
    top: 60px; background: var(--card-dark);
    display: flex; flex-direction: column; align-items: center;
  }
  .brand { margin-top: 150px; display: flex; align-items: center; gap: 14px; }
  .brand__mark { width: 26px; height: 26px; background: var(--brand-red); }
  .brand__name {
    font-family: "Oswald", sans-serif; font-weight: 600; font-size: 52px;
    letter-spacing: 3px; text-transform: uppercase; color: var(--ink-light);
    line-height: 1;
  }
  .promo {
    margin-top: 58px;
    font-family: "Oswald", sans-serif; font-weight: 500; font-size: 19px;
    letter-spacing: 1.6px; text-transform: uppercase; color: var(--ink-light);
  }
  /* Front side */
  .card--front { top: 540px; background: var(--card-light); }
  .identity { position: absolute; right: 440px; top: 150px; text-align: right; }
  .identity__name {
    font-family: "Oswald", sans-serif; font-weight: 500; font-size: 26px;
    text-transform: uppercase; color: var(--ink-dark); line-height: 1.15;
    white-space: nowrap;
  }
  .identity__name .accent { color: var(--brand-red); }
  .identity__role {
    font-family: "Oswald", sans-serif; font-weight: 500; font-size: 16px;
    color: var(--ink-dark); letter-spacing: 1px;
  }
  .divider {
    position: absolute; left: 278px; top: 146px; width: 2px; height: 82px;
    background: var(--brand-red);
  }
  .contacts {
    position: absolute; left: 296px; top: 146px; list-style: none;
    font-family: "Work Sans", sans-serif; font-size: 17px; color: var(--ink-mid);
  }
  .contacts li { display: flex; align-items: center; gap: 10px; height: 27px; }
  .contacts svg { width: 15px; height: 15px; flex: none; }
  .contacts .accent { color: var(--brand-red); }
  .address {
    position: absolute; left: 0; right: 0; top: 300px; text-align: center;
    font-family: "Work Sans", sans-serif; font-size: 17px; color: var(--ink-mid);
    letter-spacing: 0.5px;
  }
</style>
</head>
<body>
<main class="canvas">
  <section class="card card--back">
    <div class="brand">
      <span class="brand__mark"></span>
      <span class="brand__name">Quorvanex</span>
    </div>
    <p class="promo">Sign up on our website for a coupon code</p>
  </section>

  <section class="card card--front">
    <div class="identity">
      <p class="identity__name">Lorraine <span class="accent">K. Vestal</span></p>
      <p class="identity__role">CEO</p>
    </div>
    <span class="divider"></span>
    <ul class="contacts">
      <li>
        <svg viewBox="0 0 16 16" aria-hidden="true"><path fill="#e0262b" d="M2 5c0-2 3-3 6-3s6 1 6 3v1h-3V5H5v1H2zM4 7h8l2 6H2zM8 8.5a2 2 0 1 0 0 4 2 2 0 0 0 0-4z"/></svg>
        <span>555.417.3820</span>
      </li>
      <li>
        <svg viewBox="0 0 16 16" aria-hidden="true"><rect x="1" y="3" width="14" height="10" fill="#e0262b"/><path d="M1 3l7 6 7-6" fill="none" stroke="#fff" stroke-width="1.3"/></svg>
        <span>LVestal@Quorvanexco.com</span>
      </li>
      <li>
        <svg viewBox="0 0 16 16" aria-hidden="true"><circle cx="9.5" cy="6.5" r="4.5" fill="none" stroke="#e0262b" stroke-width="2"/><path d="M6.3 9.7L1.5 14.5" stroke="#e0262b" stroke-width="2.4"/></svg>
        <span>www.<span class="accent">quorvanexco</span>.com</span>
      </li>
    </ul>
    <p class="address">P.O. Box 47315 Larkfield, Ondera 00000</p>
  </section>
</main>
</body>
</html>
```